Redesign This Psychology Website

We would like a slight redesign of this successful psychology (relationship counselling) website:

www.TheKelvaleClinic.com.au

We are updating the website, and we'd like a slight refresh of the design and style.

Please keep to very similar colours, and use the same logo. We're looking for around 10 page templates, however the main one is the home page.

Keep in mind, this website already converts quite well, so we want a new, fresh design in keeping with this one. Please don't bother designing something too extremely different.

thanks :)

Target Market(s)

couples who are looking for relationship counselling. Men and women, 25 - 70, across Australia

Industry/Entity Type

Psychology

Number of Pages Required

5+ page

Font styles to use
Sans Serif

Colors
87cfc6
b7a5cd
ec1f27
ffffff
cee9f5

Requirements
Must have
• a similar look to the current design, just looking for a slight refresh.
• Search bar
• Areas for lots of photos
• same logo
• lots of content areas
Nice to have
• great content areas, where we can display a lot of content and our areas.
Should not have
• no colors like orange, etc.
• should not have a totally different feel.

```html
<!DOCTYPE html>
<html lang="en">
<head>
<meta charset="utf-8">
<title>The Kelvale Clinic – Our Blogs</title>
<link href="https://fonts.googleapis.com/css2?family=Mulish:wght@400;600;700&family=Open+Sans:wght@400;600&display=swap" rel="stylesheet">
<style>
:root{
  --teal:#87cfc6;
  --teal-deep:#6dbfb7;
  --link:#10858f;
  --purple:#b7a5cd;
  --red:#ec1f27;
  --sky:#cee9f5;
  --ink:#222;
  --grey:#8a8a8a;
  --line:#dcdcdc;
  --foot:#f3f3f3;
}
*{box-sizing:border-box;margin:0;padding:0}
html,body{width:1200px;height:2889px;overflow:hidden;background:#fff}
body{position:relative;font-family:"Open Sans",Arial,sans-serif;color:var(--ink)}
.abs{position:absolute}
a{color:inherit;text-decoration:none}

.topbar{left:0;top:0;width:1200px;height:38px;background:#f2f2f2;border-bottom:1px solid #e3e3e3;font-family:"Mulish",sans-serif;font-size:14px;color:#555}
.topbar .assoc{position:absolute;left:132px;top:9px}
.topbar .util{position:absolute;right:98px;top:0;display:flex;height:38px}
.topbar .util a{padding:0 13px;line-height:38px;border-left:1px solid #ddd}

.header{left:0;top:38px;width:1200px;height:124px}
.brand{position:absolute;left:118px;top:28px;display:flex;align-items:center;gap:12px}
.brand .dot{width:48px;height:48px;border-radius:50%;background:var(--link)}
.brand .name{font-family:"Mulish",sans-serif;font-weight:600;font-size:30px;color:var(--link);line-height:1}
.search{position:absolute;left:456px;top:46px;width:358px;height:40px;border:1px solid #ddd;border-radius:3px;font-size:13px;color:#aaa;padding:11px 0 0 36px}
.search svg{position:absolute;left:12px;top:12px}
.call{position:absolute;right:145px;top:40px;text-align:right;font-family:"Mulish",sans-serif}
.call .lbl{color:var(--teal);font-size:17px}
.call .num{color:var(--link);font-size:24px;font-weight:700;display:flex;align-items:center;gap:8px}

.nav{left:0;top:162px;width:1200px;height:65px;background:linear-gradient(var(--teal),var(--teal-deep));display:flex;padding-left:112px;font-family:"Mulish",sans-serif;font-weight:700;font-size:16px;color:#fff;text-transform:uppercase}
.nav a{display:flex;align-items:center;padding:0 10px;border-right:1px solid rgba(255,255,255,.45);line-height:1.05}

.hero{left:0;top:227px;width:1200px;height:328px;background:linear-gradient(100deg,#6b4a3a 0%,#c9967a 35%,#e6c3a8 55%,#b9704c 80%,#7a4530 100%)}
.hero h1{position:absolute;left:127px;top:170px;font-family:"Mulish",sans-serif;font-weight:600;font-size:37px;color:#fff;letter-spacing:.5px}

.section-title{font-family:"Mulish",sans-serif;font-weight:400;font-size:29px;color:#222}
.grid{display:grid;grid-template-columns:300px 300px;column-gap:20px}
.post h3{font-size:16px;font-weight:600;color:var(--link);line-height:22px;margin-bottom:12px}
.post p{font-size:13px;color:var(--grey);line-height:22px;margin-bottom:10px}
.post .more{font-size:13px;color:var(--red)}

.tabs{display:flex;gap:30px;font-family:"Mulish",sans-serif;font-size:17px;color:#222}
.tabs .on{color:var(--link);border-bottom:2px solid var(--link);padding-bottom:8px}

.finder{left:767px;top:599px;width:300px;height:360px;background:var(--purple);padding:26px 28px;color:#fff}
.finder h2{font-family:"Mulish",sans-serif;font-weight:700;font-size:23px;text-align:center;line-height:30px}
.finder h2 span{display:flex;align-items:center;justify-content:center;gap:12px}
.finder h2 span::before,.finder h2 span::after{content:"";width:30px;height:1px;background:#fff}
.finder label{display:block;font-size:13px;margin:18px 0 4px}
.finder .field{height:34px;background:#fff;border-radius:2px;font-size:12px;color:#888;padding:9px 12px;position:relative}
.finder .btn{margin-top:16px;height:38px;background:var(--red);color:#fff;text-align:center;line-height:38px;font-family:"Mulish",sans-serif;font-weight:700;font-size:16px}

.card{left:774px;width:300px;height:115px;border:1px solid var(--line);display:flex;background:#fff}
.card .pic{width:150px;height:113px;flex:none}
.card .txt{padding:14px 10px 0 14px;font-size:14px;line-height:19px;color:#222}
.card .txt small{display:block;color:var(--teal);font-size:11px;margin-top:6px}

.footer{left:0;top:2519px;width:1200px;height:303px;background:var(--foot);border-top:1px solid #e6e6e6}
.footer .brand{left:140px;top:98px}
.fcol{position:absolute;top:70px;font-size:13px;color:#555;line-height:27px}
.fcol h4{font-family:"Mulish",sans-serif;font-weight:700;font-size:16px;color:var(--link);margin-bottom:6px}
.socials{display:flex;gap:8px;margin-top:8px}
.socials i{width:32px;height:32px;border-radius:50%;display:block}
.bottom{left:0;top:2822px;width:1200px;height:67px;background:#ececec;text-align:center;line-height:67px;font-size:12px;color:#666}
</style>
</head>
<body>

<div class="abs topbar">
  <a class="assoc" href="#">Join Our Assoicate Program →</a>
  <nav class="util"><a href="#">Home</a><a href="#">Cart</a><a href="#">Blog</a><a href="#">Resources</a><a href="#">Contact</a></nav>
</div>

<header class="abs header">
  <div class="brand"><span class="dot"></span><span class="name">The Kelvale Clinic</span></div>
  <div class="search"><svg width="14" height="14" viewBox="0 0 14 14"><circle cx="6" cy="6" r="4.5" fill="none" stroke="#aaa" stroke-width="1.5"/><line x1="9.5" y1="9.5" x2="13" y2="13" stroke="#aaa" stroke-width="1.5"/></svg>Search here</div>
  <div class="call">
    <div class="lbl">Call Us Now</div>
    <div class="num"><svg width="22" height="22" viewBox="0 0 24 24"><path d="M6 2l4 4-2 3c1.5 3 4 5.5 7 7l3-2 4 4-3 4C10 21 3 14 2 5z" fill="none" stroke="#ec1f27" stroke-width="1.8"/></svg>1300 555 014</div>
  </div>
</header>

<nav class="abs nav">
  <a href="#">Counselling<br>Types</a>
  <a href="#">Relationship Counselling<br>Locations</a>
  <a href="#">Sex Therapy<br>Locations</a>
  <a href="#">About Us</a>
  <a href="#">Quizzes</a>
  <a href="#">FAQ'S</a>
  <a href="#" style="border:none">Contact</a>
</nav>

<section class="abs hero" role="img" aria-label="Smiling couple making a heart shape with their hands">
  <h1>OUR BLOGS</h1>
</section>

<section class="abs" style="left:127px;top:600px;width:630px">
  <h2 class="section-title">Relationship Help and Advice</h2>
</section>

<div class="abs grid" style="left:130px;top:670px;row-gap:0">
  <article class="post" style="height:174px"><h3>Ending Your Relationship With Respect and Even a Little Kindness</h3><p>Ending Your Relationship With Respect and Even a Little Kindness</p><a class="more" href="#">Read More</a></article>
  <article class="post"><h3>Is one of you an Intimacy Withholder?</h3><p>Do you feel like strangers? or just flat mates?One of the most important aspects of a marriage and a...</p><a class="more" href="#">Read More</a></article>
  <article class="post" style="height:194px"><h3>Keys to being Psychologically Healthy (and therefore having healthy relationships)</h3><p>Ending Your Relationship With Respect and Even a Little Kindness</p><a class="more" href="#">Read More</a></article>
  <article class="post"><h3>Would You Know If You're In An Emotionally Abusive Relationship?</h3><p>Ending Your Relationship With Respect and Even a Little Kindness</p><a class="more" href="#">Read More</a></article>
  <article class="post" style="height:173px"><h3>Have you lost yourself in your relationship?</h3><p>Ending Your Relationship With Respect and Even a Little Kindness</p><a class="more" href="#">Read More</a></article>
  <article class="post"><h3>How do I contribute to our relationship problem?</h3><p>Your Enneagram Profile If you really want to look in depth at why the two of you have the</p><a class="more" href="#">Read More</a></article>
  <article class="post" style="height:183px"><h3>Keys to being Psychologically Healthy (and therefore having healthy relationships)</h3><p>Ending Your Relationship With Respect and Even a Little Kindness</p><a class="more" href="#">Read More</a></article>
  <article class="post"><h3>Why relationships go wrong</h3><p>Relationships can be the most rewarding and most frustrating areas of our lives. Very few of us have been...</p><a class="more" href="#">Read More</a></article>
  <article class="post" style="height:193px"><h3>Keys to being Psychologically Healthy (and therefore having healthy relationships)</h3><p>Ending Your Relationship With Respect and Even a Little Kindness</p><a class="more" href="#">Read More</a></article>
  <article class="post"><h3>Would You Know If You're In An Emotionally Abusive Relationship?</h3><p>Ending Your Relationship With Respect and Even a Little Kindness</p><a class="more" href="#">Read More</a></article>
  <article class="post"><h3>Have you lost yourself in your relationship?</h3><p>Ending Your Relationship With Respect and Even a Little Kindness</p><a class="more" href="#">Read More</a></article>
  <article class="post"><h3>How do I contribute to our relationship problem?</h3><p>Your Enneagram Profile If you really want to look in depth at why the two of you have the</p><a class="more" href="#">Read More</a></article>
</div>

<section class="abs" style="left:127px;top:1756px;width:630px">
  <h2 class="section-title">Sex Help and Advice</h2>
  <div class="tabs" style="margin-top:28px"><span class="on">FOR WOMEN</span><span>FOR MEN</span><span>FOR COUPLE</span></div>
</section>

<div class="abs grid" style="left:125px;top:1884px">
  <article class="post" style="height:184px"><h3>Difficulty Orgasming: How can I experience more pleasure?</h3><p>Is Your Orgasm Hard Work or Impossible? About 10% of women are non-orgasmic. It is between 5 to 10 times harder...</p><a class="more" href="#">Read More</a></article>
  <article class="post"><h3>Low libido in women: Why have I lost my desire?</h3><p>Generally women have far more blocks to sexual fulfillment than men. That's not really surprising when you think of...</p><a class="more" href="#">Read More</a></article>
  <article class="post" style="height:198px"><h3>Tantra vs Porn – Learning How To Be Intimate</h3><p>What if studying tantra could heal our addiction to Porn? What if tapping into our natural abilities to experience...</p><a class="more" href="#">Read More</a></article>
  <article class="post"><h3>Sensual touch: the cornerstone of a great sex life.</h3><p>Do you lovingly touch your partner, children, friends or family? Often? Ever wondered why people who recoil from touch</p><a class="more" href="#">Read More</a></article>
  <article class="post"><h3>Maintaining desire: Keeping sex exciting in a long term relationship.</h3><p>What if studying tantra could heal our addiction to Porn? What if tapping into our natural abilities to experience...</p><a class="more" href="#">Read More</a></article>
  <article class="post"><h3>Differing libidos: How to manage them in a healthy way.</h3><p>Do you lovingly touch your partner, children, friends or family? Often? Ever wondered why people who recoil from touch</p><a class="more" href="#">Read More</a></article>
</div>

<svg class="abs" style="left:396px;top:2450px" width="40" height="24" viewBox="0 0 40 24"><polyline points="3,4 20,20 37,4" fill="none" stroke="#c4c4c4" stroke-width="4"/></svg>

<aside class="abs finder">
  <h2>Find Our Psychologist<span>Near You</span></h2>
  <label>Type of Counselling</label>
  <div class="field">Select<svg style="position:absolute;right:12px;top:13px" width="10" height="7" viewBox="0 0 10 7"><polyline points="1,1 5,5 9,1" fill="none" stroke="#888" stroke-width="1.4"/></svg></div>
  <label>Location</label><div class="field"></div>
  <label>Postcode</label><div class="field"></div>
  <div class="btn">SEARCH</div>
</aside>

<div class="abs card" style="top:992px"><div class="pic" role="img" aria-label="Two hands held together" style="background:linear-gradient(135deg,#8a6a58,#d2b49c)"></div><div class="txt">What can I do if I'm living with a Narcissist?<small>Read More</small></div></div>
<div class="abs card" style="top:1119px"><div class="pic" role="img" aria-label="Upset woman with a partner gesturing" style="background:linear-gradient(135deg,#3a2a28,#a77a68)"></div><div class="txt">Are You Living With a Steamroller?<small>Read More</small></div></div>
<div class="abs card" style="top:1244px"><div class="pic" role="img" aria-label="Couple sitting apart on a sofa" style="background:linear-gradient(135deg,#5d4a40,#c9b7a5)"></div><div class="txt">Did Your Relationship Start on Rocky Ground?<small>Read More</small></div></div>
<div class="abs card" style="top:1387px"><div class="pic" role="img" aria-label="Couple lying in bed" style="background:linear-gradient(135deg,#c8a58c,#efe0d2)"></div><div class="txt">Why am I with a Narcissist?<small>Read More</small></div></div>
<div class="abs card" style="top:1514px"><div class="pic" role="img" aria-label="Couple talking with a counsellor" style="background:linear-gradient(135deg,#6c7a86,#c6ccd2)"></div><div class="txt">Letter for a Partner Doubtful About Relationship Counselling<small>Read More</small></div></div>
<div class="abs card" style="top:1643px"><div class="pic" role="img" aria-label="Couple arm wrestling at a table" style="background:linear-gradient(135deg,#c27a5a,#ead2b8)"></div><div class="txt">What Are You Like In a Relationship?<small>Read More</small></div></div>
<div class="abs card" style="top:1772px"><div class="pic" role="img" aria-label="Couple facing each other" style="background:linear-gradient(135deg,#3c3330,#9a8070)"></div><div class="txt">How Do I Know If I'm With a Narcissist?<small>Read More</small></div></div>
<div class="abs card" style="top:1899px"><div class="pic" role="img" aria-label="Couple embracing outdoors" style="background:linear-gradient(135deg,#9a4a38,#e2b899)"></div><div class="txt">Do You Wonder Why You and Your Partner Are Together?<small>Read More</small></div></div>
<div class="abs card" style="top:2026px"><div class="pic" role="img" aria-label="Professional woman at work" style="background:linear-gradient(135deg,#7a6a5e,#d6cbbf)"></div><div class="txt">Is Your Pursuit of Success Sabotaging Your Relationships That Matter Most?<small>Read More</small></div></div>

<footer class="abs footer">
  <div class="brand"><span class="dot"></span><span class="name">The Kelvale Clinic</span></div>
  <div class="fcol" style="left:462px"><h4>QUICK LINKS</h4>Home<br>About Us<br>Our Blogs<br>Shop Cart<br>Contact Us</div>
  <div class="fcol" style="left:630px"><h4>RESOURCES</h4>Counselling Type<br>Sex Therapy<br>Quizzes<br>FAQ<br>Relationship Counselling</div>
  <div class="fcol" style="left:834px"><h4>CONTACT US</h4>42 Harbour View Road Suite 7<br>1300 555 014<br>Email: info@companyname.com
    <div class="socials"><i style="background:#4aa3df"></i><i style="background:#2f5597"></i><i style="background:#1f6fa8"></i><i style="background:#d9452f"></i></div>
  </div>
</footer>
<div class="abs bottom">© 2017 Company Name &nbsp;All right reserved</div>

</body>
</html>
```